A unique communication angle to crowdfunding

Looking for a fresh redesign of a crowd funding website that deals in real estate. I already have the content, but am looking to take the design to the next level.

Existing real estate crowd funding sites focus on the real estate. I want to explore communication angle that:
- puts the investor in the centre of the communication: "become a baron"
- highlights the international nature (international properties, international investors)

There's also quite a lot of copy on the site, as we need to explain the service in quite a bit of detail. There's room to reduce the copy and replace with graphics. Could also consider clicking to see different text (see our difference section in http://galleonfairs.com)

The backend of the platform is already being worked on by a specialist crowd funding service provider.

In total there are 5 pages to be designed.

The homepage is really important. Right now it looks quite dated. It doesn't have a great layout. Note there is no mobile version of the website, so the pages need to be seen well on mobile devices. When looking at the brief, refer to the following links too:

current website:
http://pennyduke.com

some revisions made so far:
http://preview.stakeharbor.com/7K3LQ9

Attached are logo files and another file which contained copy for the pages. No need to rework the logo.

Please make sure to use the same copy in the brief on the webpages, to ensure the layouts work. Designers are free to propose images they feel work on the pages.

I would like to see if rather than tweaking the pages, it's possible to come up with a better design concept. If the 5 pages are accepted, there's a chance I'll request an additional 4 pages.
Updates

Please note the font used in the logo is called "harabara" in case you decide to use it in any of the titles, etc.

Please note there is one additional page for which we would like to review designs. Note the page would be a template to be used on all future real estate detail pages. Here is an example of the current design for reference:

http://pennyduke.com/projects/view/14

In total there are 5 page designs required, (homepage + 4)

Thank you

FYI -

Just a quick note to give information from similar UK real estate crowdfunding sites:
http://www.housewalrus.co.uk
http://tiderock.co.uk
https://www.fundquarry.com

Of the above, only tiderock has a nice clean looking landing page. Information is clear and well laid out.

Hi all, just uploaded a new file in the brief. Contains some comments and a website reference. I thought it may help to explain how we could convey international aspect as well as how we could convey images in a more modern way. This is an option you can consider, but its entirely up to you how how answer the brief. Thanks!

Reason: As requested by some designers needing more time to complete their work. Continue to share your work in progress and receive timely feedback before the deadline.

We would like to let you know that we have just shortlisted the best designs. Together with that, we have also passed some detailed feedback to all designers who weren't shortlisted. If we didn't contact you, please let us know. If you haven't submitted a design or are working on revisions, please note these will no longer be taken into account now. We hope you understand that we need to close the project today. Thank you all once again for your great work and design concepts. Here's hoping we meet again on a future design brief. Cheers, pennyduke team.

Target Market(s)

At the moment, only rich are able to buy real estate. With this service, anyone can become a landlord. Target buyers:

Young professionals, looking to diversify from stock market and lower risk
People nearing retirement, looking for stable rental incomes
Retirees - looking to supplement pensions with possibility of capital gains
Parents - looking for a way to save long term for their children (instead of low interest paying bank accounts)

Industry/Entity Type

Communication

Font styles to use
Sans Serif
Other font styles liked:
• harabara

Colors
add136
f5f9eb
959595
000000

Requirements
Must have
• Overall, the site must convey "whoever you are, you too can become a landlord", and that you don't need to be wealthy to invest in real estate. See

Communication should put the investor (or the baron) at the centre. The investor can be any of those described in the target market.

Show the aspirational side of property ownership.

In addition to the investor/baron character, the second main theme is international. No other real estate crowdfunding website highlights this.
Nice to have
• Banner could show different consumer types, to illustrate that the service can appeal to many different profiles. Refer to attached file "home page reference - plainasbread.com" as an example of how this could be done.

Aim to show the international side of the service. Properties around the world, investors around the world.

```html
<!DOCTYPE html>
<html lang="en">
<head>
<meta charset="utf-8">
<title>pennyduke – Build your property portfolio</title>
<link href="https://fonts.googleapis.com/css2?family=Open+Sans:wght@400;600;700&family=Varela+Round&display=swap" rel="stylesheet">
<style>
:root{
  --green:#8cc63f;
  --green-dark:#79b02f;
  --ink:#333333;
  --grey:#959595;
  --grey-light:#e9e9e9;
  --band:#ededed;
  --charcoal:#4a4a4a;
  --dark:#2f2f2f;
  --paper:#ffffff;
  --footer-paper:#f3f3f3;
}
*{box-sizing:border-box;margin:0;padding:0}
html,body{width:1200px;height:3000px;overflow:hidden;background:var(--paper)}
body{font-family:"Open Sans",Arial,sans-serif;color:var(--ink);position:relative}
.heading{font-family:"Varela Round","Open Sans",sans-serif;font-weight:400}

/* header */
.site-header{position:absolute;left:0;top:0;width:1200px;height:96px;background:var(--paper);border-bottom:1px solid #e4e4e4}
.brand{position:absolute;left:156px;top:24px;display:flex;align-items:center;gap:10px}
.brand-dot{width:40px;height:40px;border-radius:50%;background:var(--green)}
.brand-name{font-family:"Varela Round",sans-serif;font-size:24px;color:var(--green)}
.social{display:flex;align-items:center;gap:8px}
.social-label{font-size:13px;color:#666;margin-right:6px}
.social-square{width:30px;height:26px;background:var(--green)}
.social-square.alt{background:#666}
.header-social{position:absolute;left:620px;top:22px}
.search{position:absolute;left:808px;top:22px;width:246px;height:28px;display:flex}
.search-field{flex:1;background:#eeeeee;font-size:11px;color:#999;padding:7px 10px}
.search-btn{width:38px;background:#555;display:flex;align-items:center;justify-content:center}
.main-nav{position:absolute;right:146px;top:64px;display:flex;gap:24px;font-size:11px;font-weight:600;color:#666;text-transform:uppercase}
.main-nav span{padding-bottom:6px}
.main-nav .active{color:#333;border-bottom:3px solid var(--green)}

/* hero */
.hero{position:absolute;left:0;top:96px;width:1200px;height:388px;
  background:linear-gradient(180deg,#b7bcc0 0%,#9aa0a4 35%,#6f6a62 70%,#3e3a35 100%)}
.hero-caption{position:absolute;left:188px;top:156px;width:500px;height:80px;background:rgba(40,40,40,.72);padding:12px 16px}
.hero-title{font-size:24px;color:var(--green);font-family:"Varela Round",sans-serif}
.hero-sub{font-size:14px;color:var(--green);margin-top:6px}
.hero-arrow{position:absolute;top:172px;width:46px;height:46px;border-radius:50%;background:var(--green);border:2px solid #e8f2d8}
.hero-dots{position:absolute;left:128px;top:368px;display:flex;gap:8px}
.hero-dots i{width:9px;height:9px;border-radius:50%;background:#ccc;display:block}
.hero-dots i:first-child{background:var(--green)}

/* intro */
.intro{position:absolute;left:0;top:484px;width:1200px;text-align:center}
.intro h1{margin-top:46px;font-size:29px;color:var(--green)}
.intro .rule{width:210px;height:2px;background:#e2e2e2;margin:14px auto 18px}
.intro p{font-size:13.5px;color:#666;line-height:24px;margin-bottom:22px}
.intro b{color:var(--green);font-weight:400}

/* join band */
.join-band{position:absolute;left:0;top:788px;width:1200px;height:357px;background:var(--band)}
.skyline{position:absolute;left:0;bottom:0;width:1200px;height:120px;background:linear-gradient(180deg,#5a5a5a,#454545)}
.join-card{position:absolute;top:50px;width:368px;height:152px;background:var(--paper);border:1px solid #dcdcdc}
.join-icon{position:absolute;left:18px;top:26px;width:80px;height:80px;border-radius:50%;background:#444}
.join-card h3{position:absolute;left:118px;top:26px;font-size:21px;color:var(--green)}
.join-card p{position:absolute;left:118px;top:58px;width:230px;font-size:13px;line-height:23px;color:#666}
.join-btn{position:absolute;top:206px;width:368px;height:46px;background:var(--green);color:#fff;font-size:20px;text-align:center;line-height:46px;border-bottom:3px solid var(--green-dark);z-index:2}

/* featured projects */
.projects{position:absolute;left:0;top:1145px;width:1200px;height:647px;text-align:center}
.projects h2{margin-top:46px;font-size:21px;color:var(--green)}
.projects .lead{margin-top:16px;font-size:13px;line-height:26px;color:#666}
.projects .lead b{color:var(--green);font-weight:600}
.project-card{position:absolute;top:167px;width:290px;height:416px;background:var(--paper);border:1px solid #dedede;box-shadow:0 1px 6px rgba(0,0,0,.12);text-align:left}
.project-photo{height:206px;background:linear-gradient(180deg,#7fb3e0 0%,#b9d6ee 45%,#8a7c6a 62%,#6d8f3f 100%)}
.tag-price{position:absolute;left:0;top:0;background:var(--green);color:#fff;font-size:10px;font-weight:700;padding:5px 8px}
.tag-new{position:absolute;left:0;top:30px;background:#555;color:#dfe9c9;font-size:9px;font-weight:600;padding:4px 8px}
.project-title{margin:14px 10px 0;font-size:15px;color:var(--green);padding-bottom:10px;border-bottom:1px solid #e4e4e4}
.project-desc{margin:8px 10px 0;font-size:11px;line-height:18px;color:#555}
.funded{margin:20px 10px 0;font-size:12px;font-weight:600;color:#444;border-top:1px solid #e4e4e4;padding-top:8px}
.bar{margin:4px 10px 0;height:20px;border:1px solid #ccc;background:#f4f4f4}
.bar-fill{height:100%;background:linear-gradient(180deg,#9fd052,#7db435);font-size:11px;font-weight:600;color:#333;text-align:right;padding-right:10px;line-height:18px}
.project-link{margin-top:12px;text-align:center;font-size:12px;font-weight:600;color:#666}
.project-card.first .project-link{color:var(--green)}

/* community */
.community{position:absolute;left:0;top:1792px;width:1200px;height:422px;
  background:radial-gradient(ellipse at 50% 40%,#5a5a5a 0%,#3a3a3a 55%,#252525 100%);text-align:center}
.community h2{margin-top:54px;font-size:20px;color:var(--green)}
.community .lead{margin-top:12px;font-size:15px;line-height:24px;color:#7c7c7c}
.stat{position:absolute;top:210px;width:260px;text-align:center}
.stat-icon{display:block;margin:0 auto 6px}
.stat-value{font-size:20px;font-weight:700;color:var(--green);line-height:24px;font-family:"Varela Round",sans-serif}
.stat-caption{margin-top:30px;font-size:15px;line-height:24px;color:#cfcfcf}

/* featured in */
.press{position:absolute;left:144px;top:2272px;width:910px;height:194px;border:1px solid #dedede}
.press-tab{position:absolute;left:376px;top:-18px;width:176px;height:36px;background:var(--green);color:#fff;font-size:16px;text-align:center;line-height:36px}
.press-badge{position:absolute;height:26px;background:#cfcfcf;border-radius:3px}

/* footer */
.footer-bar{position:absolute;left:0;top:2520px;width:1200px;height:72px;background:var(--charcoal)}
.footer-social{position:absolute;left:144px;top:22px}
.footer-social .social-label{color:var(--green);font-size:16px}
.footer-social .social-square{background:transparent;border:2px solid var(--green)}
.copyright{position:absolute;right:146px;top:26px;color:var(--green);font-size:13px}
.footer-text{position:absolute;left:0;top:2592px;width:1200px;height:408px;background:var(--footer-paper)}
.footer-text p{position:absolute;left:144px;font-size:12.5px;line-height:20px;color:#555}
.footer-text strong{color:var(--green)}
.parent-name{position:absolute;left:842px;top:24px;font-size:22px;font-weight:600;color:#555;line-height:28px}
</style>
</head>
<body>

<header class="site-header">
  <div class="brand"><span class="brand-dot"></span><span class="brand-name">pennyduke.com</span></div>
  <div class="social header-social">
    <span class="social-label">Follow us on</span>
    <span class="social-square"></span><span class="social-square alt"></span>
  </div>
  <div class="search">
    <div class="search-field">Search...</div>
    <div class="search-btn">
      <svg width="14" height="14" viewBox="0 0 14 14"><circle cx="6" cy="6" r="4.2" fill="none" stroke="#fff" stroke-width="2"/><line x1="9" y1="9" x2="13" y2="13" stroke="#fff" stroke-width="2"/></svg>
    </div>
  </div>
  <nav class="main-nav">
    <span class="active">Home</span><span>Sign in</span><span>How it works</span><span>Discover a project</span><span>The baron blog</span><span>Find out more</span>
  </nav>
</header>

<section class="hero" role="img" aria-label="Young investor in a suit working on a laptop on a rooftop above a city skyline">
  <div class="hero-arrow" style="left:94px">
    <svg width="42" height="42" viewBox="0 0 42 42"><path d="M24 13 L16 21 L24 29" fill="none" stroke="#fff" stroke-width="3"/></svg>
  </div>
  <div class="hero-caption">
    <div class="hero-title">Build your property portfolio</div>
    <div class="hero-sub">Join our international community. Pool with friends. Share the gains.</div>
  </div>
  <div class="hero-arrow" style="left:1060px">
    <svg width="42" height="42" viewBox="0 0 42 42"><path d="M18 13 L26 21 L18 29" fill="none" stroke="#fff" stroke-width="3"/></svg>
  </div>
  <div class="hero-dots"><i></i><i></i><i></i><i></i></div>
</section>

<section class="intro">
  <h1 class="heading">Reconstructing a property ladder that's strong and fair</h1>
  <div class="rule"></div>
  <p>By harnessing the power of crowds, it's possible to become a landlord in locations around the world. Forget the burden of<br>financing <b>100%</b> of the purchase.</p>
  <p>Leave the day to day management of your property portfolio to us.</p>
  <p>Start with <b>1%</b> in a project and plan your steps to becoming a true baron</p>
</section>

<section class="join-band">
  <div class="join-card" style="left:202px">
    <div class="join-icon"></div>
    <h3 class="heading">Find properties</h3>
    <p>Sign up to browse the portfolio. Your journey to becoming a real estate baron starts here.</p>
  </div>
  <div class="join-card" style="left:630px">
    <div class="join-icon"></div>
    <h3 class="heading">Find Buyers</h3>
    <p>Submit a property or development and raise funds from our real estate barons.</p>
  </div>
  <div class="join-btn heading" style="left:202px">Become a member</div>
  <div class="join-btn heading" style="left:630px">Submit a property</div>
  <div class="skyline" role="img" aria-label="Silhouette of world city skylines"></div>
</section>

<section class="projects">
  <h2 class="heading">Featured Projects</h2>
  <p class="lead">Brief details of new and popular projects. To view full listings, you will be required to<br>sign up and <b>become a member.</b></p>

  <article class="project-card first" style="left:144px">
    <div class="project-photo" role="img" aria-label="Brick family house with a white garage"></div>
    <span class="tag-price">From GBP 3,600</span><span class="tag-new">New Launch</span>
    <h4 class="project-title">21 Wapping Lane LONDON E1</h4>
    <p class="project-desc">Lorem Ipsum is simply dummy text of the printing and typesetting industry. Lorem Ipsum has been the industry's .</p>
    <div class="funded">Funded</div>
    <div class="bar"><div class="bar-fill" style="width:50%">50%</div></div>
    <div class="project-link">See Project Details</div>
  </article>

  <article class="project-card" style="left:455px">
    <div class="project-photo" role="img" aria-label="Cream suburban house with a double garage"></div>
    <span class="tag-price">From GBP 3,600</span><span class="tag-new">New Launch</span>
    <h4 class="project-title">21 Wapping Lane LONDON E1</h4>
    <p class="project-desc">Lorem Ipsum is simply dummy text of the printing and typesetting industry. Lorem Ipsum has been the industry's .</p>
    <div class="funded">Funded</div>
    <div class="bar"><div class="bar-fill" style="width:75%">75%</div></div>
    <div class="project-link">See Project Details</div>
  </article>

  <article class="project-card" style="left:764px">
    <div class="project-photo" role="img" aria-label="Mediterranean villa with a tower among trees"></div>
    <span class="tag-price">From GBP 3,600</span><span class="tag-new">New Launch</span>
    <h4 class="project-title">21 Wapping Lane LONDON E1</h4>
    <p class="project-desc">Lorem Ipsum is simply dummy text of the printing and typesetting industry. Lorem Ipsum has been the industry's .</p>
    <div class="funded">Funded</div>
    <div class="bar"><div class="bar-fill" style="width:40%">40%</div></div>
    <div class="project-link">See Project Details</div>
  </article>
</section>

<section class="community" role="img" aria-label="Dark aerial view of a city with a faint world map">
  <h2 class="heading">Be Part of a Growing International Community</h2>
  <p class="lead">Gain access to new projects in world class cities and join our growing community of<br>international landlords.</p>

  <div class="stat" style="left:146px">
    <svg class="stat-icon" width="14" height="20" viewBox="0 0 14 20"><path d="M7 0C3 0 0 3 0 7c0 5 7 13 7 13s7-8 7-13c0-4-3-7-7-7z" fill="#8cc63f"/><circle cx="7" cy="7" r="2.6" fill="#3a3a3a"/></svg>
    <div class="stat-value">3,200 barons<br>in 6 countries</div>
    <div class="stat-caption">A community of international<br>property barons.</div>
  </div>
  <div class="stat" style="left:470px">
    <svg class="stat-icon" width="60" height="40" viewBox="0 0 60 40"><circle cx="30" cy="10" r="8" fill="#6a6a6a"/><path d="M16 40c0-10 6-16 14-16s14 6 14 16z" fill="#6a6a6a"/><circle cx="12" cy="16" r="6" fill="#5a5a5a"/><circle cx="48" cy="16" r="6" fill="#5a5a5a"/></svg>
    <div class="stat-value" style="margin-top:4px">US$ 16.2 million</div>
    <div class="stat-caption" style="margin-top:44px">Collective buying power of<br>the pennyduke community</div>
  </div>
  <div class="stat" style="left:780px">
    <svg class="stat-icon" width="14" height="20" viewBox="0 0 14 20"><path d="M7 0C3 0 0 3 0 7c0 5 7 13 7 13s7-8 7-13c0-4-3-7-7-7z" fill="#8cc63f"/><circle cx="7" cy="7" r="2.6" fill="#3a3a3a"/></svg>
    <div class="stat-value">64 proposals in 6<br>countries</div>
    <div class="stat-caption">Attractive real estate from<br>around the world</div>
  </div>
</section>

<section class="press">
  <div class="press-tab heading">Featured In</div>
  <span class="press-badge" style="left:36px;top:56px;width:112px"></span>
  <span class="press-badge" style="left:180px;top:56px;width:128px"></span>
  <span class="press-badge" style="left:340px;top:54px;width:112px;height:30px"></span>
  <span class="press-badge" style="left:540px;top:58px;width:330px;height:22px"></span>
  <span class="press-badge" style="left:168px;top:130px;width:44px;height:32px"></span>
  <span class="press-badge" style="left:250px;top:134px;width:126px;height:22px"></span>
  <span class="press-badge" style="left:416px;top:128px;width:40px;height:36px"></span>
  <span class="press-badge" style="left:494px;top:126px;width:74px;height:38px"></span>
  <span class="press-badge" style="left:588px;top:132px;width:140px;height:26px"></span>
</section>

<footer>
  <div class="footer-bar">
    <div class="social footer-social">
      <span class="social-label">Follow us on</span>
      <span class="social-square"></span><span class="social-square"></span>
    </div>
    <div class="copyright">© pennyduke 2014</div>
  </div>
  <div class="footer-text">
    <span class="parent-name">Tallmast Holdings</span>
    <p style="top:20px;width:580px"><strong>Penny Duke</strong> is part of Tallmast Holdings. Tallmast Holdings is a worldwide pioneer and leader in the crowd investing, peer to peer and online investment market.</p>
    <p style="top:84px;width:912px">By accessing this site and any pages thereof, you agree to be bound by the terms and conditions. This website is only suitable, intended and available for professional or sophisticated, or similar investors in other jurisdictions, or those who are members of pennyduke community and familiar with, and willing to, accept the risks associated with private participation. Pennyduke does not endorse any of the projects that appear on this website, nor does it make any recommendations regarding the appropriateness of particular opportunities for any participant. Each potential participant must review and evaluate the projects in his or her own discretion and determine the suitability of participating.</p>
    <p style="top:204px;width:912px">This website (the "Site") is in every respect unaffiliated with any site to which it links or to any company or entity (and connected projects, investment opportunity or similar) featured on this Site, and is not meant as an endorsement of any of those companies or entities ("third parties"). Furthermore and for the avoidance of doubt, Pennyduke Limited is in no way affiliated with any third parties featured or referenced on this Site. There is no commercial relationship between Pennyduke Limited and such third parties, nor an agency arrangement or similar. If you believe your Content (including third party content) as each such term is defined in our Terms of Service has been reproduced on the Site without permission, please refer to our Terms of Service for information on how to request its removal from the Site.</p>
  </div>
</footer>

</body>
</html>
```